TALMORK

The business want a professional looking business card. We have a scetch we will add but want the extra upgrade, and would like more suggestions for variations of our business cards.

```html
<!DOCTYPE html>
<html lang="en">
<head>
<meta charset="utf-8">
<title>TALMORK business card</title>
<link href="https://fonts.googleapis.com/css2?family=Montserrat:wght@400;600;700&display=swap" rel="stylesheet">
<style>
  :root {
    --backdrop: #141414;
    --card: #1f1f1f;
    --gold: #c9a24a;
    --gold-bar: #b8913d;
    --ink-light: #f2f2f2;
  }
  * { margin: 0; padding: 0; box-sizing: border-box; }
  html, body {
    width: 1200px;
    height: 1059px;
    overflow: hidden;
    background: var(--backdrop);
    font-family: "Montserrat", sans-serif;
  }
  .canvas { position: relative; width: 1200px; height: 1059px; }
  .card {
    position: absolute;
    background: var(--card);
    border-radius: 24px;
    box-shadow: 0 14px 30px rgba(0,0,0,0.55);
    overflow: hidden;
  }
  .card-front { left: 257px; top: 89px; width: 687px; height: 390px; }
  .card-back { left: 254px; top: 547px; width: 693px; height: 393px; }

  .brand-name {
    position: absolute;
    color: var(--gold);
    font-weight: 600;
    white-space: nowrap;
  }
  .card-front .brand-name {
    left: 123px; top: 145px;
    transform: translateX(-50%);
    font-size: 24px;
    letter-spacing: 6px;
  }
  .card-back .brand-name {
    left: 50%; top: 50%;
    transform: translate(-50%, -50%);
    font-size: 46px;
    letter-spacing: 12px;
  }

  .contact-list { position: absolute; left: 38px; top: 254px; list-style: none; }
  .contact-item {
    display: flex; align-items: center;
    height: 34px;
    color: var(--ink-light);
    font-size: 18.5px;
    font-weight: 400;
    letter-spacing: 0.3px;
  }
  .contact-icon { width: 15px; height: 15px; margin-right: 10px; fill: var(--gold); }

  .person { position: absolute; right: 37px; top: 274px; text-align: right; }
  .person-name { color: var(--gold); font-size: 22px; font-weight: 700; line-height: 1.2; }
  .person-role { color: var(--ink-light); font-size: 18.5px; font-weight: 400; line-height: 1.3; }
  .accent-bar {
    position: absolute; left: 670px; top: 281px;
    width: 17px; height: 42px;
    background: var(--gold-bar);
  }
</style>
</head>
<body>
<main class="canvas">
  <section class="card card-front" aria-label="Card front">
    <div class="brand-name">TALMORK</div>

    <ul class="contact-list">
      <li class="contact-item">
        <svg class="contact-icon" viewBox="0 0 24 24" aria-hidden="true"><path d="M6.6 10.8a15.1 15.1 0 0 0 6.6 6.6l2.2-2.2a1 1 0 0 1 1-.25 11.4 11.4 0 0 0 3.6.57 1 1 0 0 1 1 1V20a1 1 0 0 1-1 1A17 17 0 0 1 3 4a1 1 0 0 1 1-1h3.5a1 1 0 0 1 1 1c0 1.25.2 2.45.57 3.57a1 1 0 0 1-.25 1z"/></svg>
        004791234567
      </li>
      <li class="contact-item">
        <svg class="contact-icon" viewBox="0 0 24 24" aria-hidden="true"><path d="M2 9l10-7 10 7v12H2zM4 10v1l8 5 8-5v-1l-8-5z"/></svg>
        talmork.llc@mailbox.com
      </li>
      <li class="contact-item">
        <svg class="contact-icon" viewBox="0 0 24 24" aria-hidden="true"><path d="M12 2a10 10 0 1 0 0 20 10 10 0 0 0 0-20zm-1 17.9A8 8 0 0 1 4.2 10H8l3 3v2l-2 2v2.9zm6.9-2.5L16 15h-2v-3l-3-3h3V6l2-1.9a8 8 0 0 1 1.9 13.3z"/></svg>
        www.talmork.llc
      </li>
    </ul>

    <div class="person">
      <div class="person-name">Ola Brekke Solvang</div>
      <div class="person-role">CEO &amp; Founder</div>
    </div>
    <div class="accent-bar"></div>
  </section>

  <section class="card card-back" aria-label="Card back">
    <div class="brand-name">TALMORK</div>
  </section>
</main>
</body>
</html>
```